Oil Field Service company needs professional business cards

Looking to clean up our current company business cards and look a little more professional. Brenwick Casing Services is a US based company that services the oil field. We deal with engineers, managers and oil rigs....................................................................................................................................................................................................................................................................................................................................................................................................

Target Market(s)

Oil and Gas professionals

Industry/Entity Type

Oil And Gas

Contact Information for Business Card

See attached photo as example

Font styles to use
Sans Serif

Colors
ec1f27

Requirements
Must have
• Company Logo, Name, Title, Cell, Office, Fax, Email.
• See attached photo
Nice to have
• External CRT, Internal CRT, Casing Crews, Torque Turn, Laydown Machine
Should not have
• Do not introduce any new pictures and keep it professional looking

```html
<!DOCTYPE html>
<html lang="en">
<head>
<meta charset="utf-8">
<title>Brenwick Casing Services – Business Card</title>
<link rel="stylesheet" href="https://fonts.googleapis.com/css2?family=Open+Sans:wght@400;600;700;800&display=swap">
<style>
  :root {
    --backdrop: #1c1d1f;
    --card-white: #ffffff;
    --brand-red: #ec1f27;
    --charcoal: #2f3134;
    --slate: #1f3b4d;
    --logo-grey: #3d4a55;
    --body-grey: #55595e;
    --contact-text: #e9eaeb;
  }
  * { box-sizing: border-box; margin: 0; padding: 0; }
  html, body {
    width: 1200px; height: 1000px; overflow: hidden;
    background: var(--backdrop);
    font-family: "Open Sans", Arial, sans-serif;
  }
  .card {
    position: absolute; left: 150px; top: 243px;
    width: 900px; height: 514px;
    border-radius: 40px; overflow: hidden;
    background: var(--card-white);
    box-shadow: 0 20px 50px rgba(0,0,0,.5);
  }
  .card-wave { position: absolute; inset: 0; width: 900px; height: 514px; }
  .holder {
    position: absolute; right: 70px; top: 62px; text-align: right;
  }
  .holder-name {
    font-weight: 700; font-size: 34px; letter-spacing: .5px;
    color: var(--slate); line-height: 1.05;
  }
  .holder-title {
    font-weight: 600; font-size: 26px; letter-spacing: .5px;
    color: var(--brand-red); line-height: 1.1;
  }
  .services {
    list-style: none; margin-top: 14px;
    font-size: 17px; line-height: 1.28; color: var(--body-grey);
  }
  .company {
    position: absolute; left: 64px; top: 178px;
    display: flex; align-items: center; gap: 14px;
  }
  .company-mark { width: 18px; height: 18px; background: var(--brand-red); }
  .company-name {
    font-weight: 800; color: var(--logo-grey); line-height: 1;
  }
  .company-name .line-main { display: block; font-size: 44px; letter-spacing: 1px; }
  .company-name .line-sub { display: block; font-size: 16px; letter-spacing: 3px; margin-top: 4px; }
  .address {
    position: absolute; left: 96px; top: 262px;
    font-size: 17px; color: var(--body-grey);
  }
  .contacts {
    position: absolute; left: 90px; top: 356px; list-style: none;
  }
  .contacts li {
    display: flex; align-items: center; gap: 18px;
    height: 34px; font-size: 19px; color: var(--contact-text);
  }
  .contacts svg { width: 18px; height: 18px; fill: none; stroke: var(--contact-text); stroke-width: 1.8; }
</style>
</head>
<body>
  <main class="card">
    <svg class="card-wave" viewBox="0 0 900 514" aria-hidden="true">
      <path d="M0,278 C300,300 640,300 900,430 L900,514 L0,514 Z" fill="var(--brand-red)"/>
      <path d="M0,298 C300,318 650,328 900,452 L900,514 L0,514 Z" fill="var(--charcoal)"/>
    </svg>

    <header class="holder">
      <h1 class="holder-name">COREY HALDANE</h1>
      <p class="holder-title">AREA MANAGER</p>
      <ul class="services">
        <li>Laydown Machine</li>
        <li>Casing Crew</li>
        <li>Mud Tools</li>
        <li>Torque Turn</li>
      </ul>
    </header>

    <div class="company">
      <span class="company-mark"></span>
      <p class="company-name"><span class="line-main">BRENWICK</span><span class="line-sub">CASING SERVICES</span></p>
    </div>
    <p class="address">Alder Ridge, OK 73990</p>

    <ul class="contacts">
      <li><svg viewBox="0 0 18 18"><rect x="5" y="1.5" width="8" height="15" rx="1.5"/><line x1="8" y1="14" x2="10" y2="14"/></svg>(555) 218 4400</li>
      <li><svg viewBox="0 0 18 18"><path d="M4 2 L7 2 L8 6 L6 7.5 C7 10 8 11 10.5 12 L12 10 L16 11 L16 14 C16 15 15 16 14 16 C8 15.5 2.5 10 2 4 C2 3 3 2 4 2 Z"/></svg>(555) 307 6182</li>
      <li><svg viewBox="0 0 18 18"><rect x="2" y="7" width="14" height="8" rx="1"/><rect x="5" y="2" width="8" height="5"/><line x1="5" y1="11" x2="13" y2="11"/></svg>(555) 218 4491</li>
      <li><svg viewBox="0 0 18 18"><rect x="1.5" y="4" width="15" height="10" rx="1"/><path d="M1.5 4.5 L9 10 L16.5 4.5"/></svg>yourname@email.com</li>
    </ul>
  </main>
</body>
</html>
```